Cloud Based Bookkeeping Website for Florists (Flower Shops)

We need a single page responsive website for a bookkeeping firm specializing in the floral industry. Our business model is based on the cloud and a goal is to attain floral clients from around the country, not only local.

Currently, we are attracted to flat illustration designs, but are concerned that they appear to informal or unprofessional. This webdesign should communicate professionalism, yet approachable, bright, attractive and modern.

The color scheme and overall design should match our designed logo, which is attached, and icon sets. We are open to new icon ideas and layout design, other than the layout we prepared and attached.

The attached layout we prepared has a holding place for a video at the top section. We own the video and can provide at a later time to insert. There is another secondary holding place for an explanation video, which we may or may not need, depending on the design your submit.

Lastly, I want to reiterate that we are open to new layout ideas.

Target Market(s)

Florists, Flower Shops

Industry/Entity Type

Bookkeeper

Number of Pages Required

2 page

Font styles to use
Sans Serif

Requirements
Must have
• Each section should be full width and screen height.
• Full page/section scrolling
• A price table
• A scrolling or fixed section displaying the third party app we work with.
• A blog page and a scrolling carousel displaying recent blog posts.
• Services section should be the six listed, but expandable to add more.
• A lead generation page, where clients can add attachments
• Must be a WordPress design so owner can easily modify and edit in the future
• Must be able to accommodate java script snippets in the header.
Nice to have
• A fixed "Contact Us" tab on the right side of the page that will lead to a contact form.

```html
<!DOCTYPE html>
<html lang="en">
<head>
<meta charset="utf-8">
<title>PetalBooks</title>
<link href="https://fonts.googleapis.com/css2?family=Nunito+Sans:wght@400;600;700&family=Open+Sans:wght@400;600;700&display=swap" rel="stylesheet">
<style>
:root{
  --orange:#e8531f;
  --teal:#4aa8c0;
  --green:#7cb342;
  --ink:#2f2f2f;
  --text:#555;
  --muted:#8a8a8a;
  --grey-bg:#ececec;
  --white:#fff;
}
*{box-sizing:border-box;margin:0;padding:0}
html,body{width:1200px;height:5325px;overflow:hidden}
body{font-family:"Open Sans",sans-serif;color:var(--text);background:var(--white);font-size:13px;line-height:1.6}
h2,h3,h4{font-family:"Nunito Sans",sans-serif;color:var(--ink);font-weight:600}
.section{position:relative;width:1200px;overflow:hidden}
.section-title{text-align:center;font-size:30px;padding-top:50px}
.btn{display:inline-block;padding:8px 22px;font-size:13px;color:var(--white);font-weight:600;border-radius:2px;text-decoration:none}
.btn-orange{background:var(--orange)}
.btn-teal{background:var(--teal)}
.btn-green{background:var(--green)}
.btn-row{text-align:center;margin-top:24px}
.btn-row .btn{margin:0 8px;min-width:100px}

/* header */
.site-header{height:100px;display:flex;align-items:center;justify-content:space-between;padding:0 70px 0 110px}
.brand{font-family:"Nunito Sans",sans-serif;font-size:30px;font-weight:600;color:var(--ink)}
.main-nav{text-align:right}
.main-nav ul{list-style:none;display:flex;gap:40px;font-family:"Nunito Sans",sans-serif;font-size:17px;color:var(--ink)}
.sub-nav{font-size:11px;color:var(--text);margin-top:4px}

/* hero */
.hero{height:540px;background:linear-gradient(135deg,#4b4a46,#8c8a82 45%,#3a3936)}
.play{position:absolute;left:50%;top:50%;width:76px;height:76px;margin:-38px 0 0 -38px}

/* why */
.why{height:425px;background:var(--white)}
.why p{width:880px;margin:18px auto 0;text-align:center;font-size:12.5px}

/* how */
.how{height:692px;background:linear-gradient(180deg,#d9dadc,#eef0f1)}
.how .video{position:relative;width:490px;height:270px;margin:24px auto 0;background:linear-gradient(135deg,#9fa6a8,#d2d5d3)}
.how p{width:720px;margin:20px auto 0;text-align:center;font-size:12.5px;color:var(--ink)}

/* services */
.services{height:799px;background:var(--white)}
.service-grid{display:grid;grid-template-columns:repeat(3,260px);column-gap:80px;row-gap:40px;justify-content:center;margin-top:50px}
.service{text-align:center}
.service-icon{width:100px;height:100px;margin:0 auto 10px;border-radius:50%;background:linear-gradient(135deg,#f3c9b8,#c9e3ea)}
.service h4{font-size:19px;font-weight:400}
.service p{font-size:11px;color:var(--muted);margin-top:6px;line-height:1.5}
.btn-outline{display:block;width:170px;margin:40px auto 0;border:1px solid var(--orange);color:var(--orange);text-align:center;padding:7px 0;font-weight:600}

/* outsourced */
.outsourced{height:504px;background:linear-gradient(135deg,#2e3033,#4d4f52);color:#e8e8e8}
.outsourced h2{color:var(--white);text-align:center;font-size:30px;padding-top:70px}
.outsourced p{width:840px;margin:18px auto 0;text-align:center;font-size:12.5px}

/* cost */
.cost{height:525px;background:var(--white)}
.cost-text{position:absolute;left:110px;top:60px;width:480px}
.cost-text h2{color:var(--teal);font-size:30px;font-weight:400}
.cost-text p{font-size:12px;margin-top:16px}
.cost-text .lead{color:var(--orange);margin-top:16px}
.cost-text ol{margin:10px 0 0 18px;font-size:13px;line-height:2.2;color:var(--ink)}
.cost-photo{position:absolute;left:640px;top:0;width:560px;height:525px;background:linear-gradient(120deg,#ffffff 0%,#d8d6d3 35%,#5c5650 70%,#e9e9e9 100%)}

/* pricing */
.pricing{height:409px;background:var(--grey-bg)}
.pricing .section-title{padding-top:44px;font-weight:400}
.price-grid{display:flex;justify-content:center;gap:60px;margin-top:28px}
.plan{width:260px;height:260px;background:var(--white);text-align:center;box-shadow:0 2px 6px rgba(0,0,0,.12)}
.plan h3{font-size:18px;font-weight:600;padding:12px 0 8px;border-bottom:1px solid #e5e5e5}
.plan.basic{border-top:4px solid var(--orange)}.plan.basic h3{color:var(--orange)}
.plan.advanced{border-top:4px solid var(--green)}.plan.advanced h3{color:var(--green)}
.plan.business{border-top:4px solid var(--teal)}.plan.business h3{color:var(--teal)}
.plan ul{list-style:none;font-size:10.5px;color:var(--muted)}
.plan li{padding:5px 0;border-bottom:1px solid #efefef}
.plan .price{font-family:"Nunito Sans",sans-serif;font-size:26px;color:var(--ink);margin-top:8px}
.plan .btn{padding:4px 24px;font-size:11px;margin-top:2px}

/* contact */
.contact{height:568px;background:var(--orange)}
.contact h2{color:var(--white);text-align:center;font-size:30px;font-weight:400;padding-top:40px}
.contact-form{display:flex;gap:24px;justify-content:center;margin-top:40px}
.fields{width:400px;display:flex;flex-direction:column;gap:4px}
.field{height:38px;border:1px solid #f3a07f;color:var(--white);font-size:11px;font-weight:600;padding:10px 12px}
.dropzone{width:390px;height:206px;border:1px solid #f3a07f;color:var(--white);font-size:11px;font-weight:600;padding:10px 12px}
.submit{display:block;width:170px;margin:24px auto 0;background:var(--teal);color:var(--white);text-align:center;padding:8px 0;font-weight:600;border:2px solid #bfe3ec}

/* partners */
.partners{height:96px;display:flex;align-items:center;justify-content:center;gap:90px;font-family:"Open Sans",sans-serif;font-weight:700;font-size:22px;color:var(--ink);border-bottom:1px solid #e5e5e5}
.partner{display:flex;align-items:center;gap:8px}
.partner i{width:18px;height:18px;border-radius:50%;background:#9a9a9a;display:inline-block}

/* blogs */
.blogs{height:518px;background:var(--white)}
.blogs .section-title{padding-top:36px;font-weight:400}
.blog-grid{display:flex;justify-content:center;gap:36px;margin-top:30px}
.post{width:300px;background:var(--white);box-shadow:0 2px 8px rgba(0,0,0,.15)}
.post-img{position:relative;height:150px;background:linear-gradient(135deg,#c9c2b8,#8d8478)}
.post-date{position:absolute;left:14px;bottom:-14px;width:52px;height:52px;background:var(--teal);color:var(--white);text-align:center;font-family:"Nunito Sans",sans-serif;font-size:22px;font-weight:700;line-height:1.2;padding-top:4px}
.post-date small{display:block;font-size:10px;font-weight:400}
.post-body{padding:30px 16px 18px}
.post-body h4{font-size:16px;font-weight:400}
.post-body p{font-size:10.5px;color:var(--muted);margin-top:6px;line-height:1.5}
.post-body a{display:inline-block;margin-top:10px;color:var(--orange);font-size:11px;font-weight:700;text-decoration:none}

/* footer */
.site-footer{height:149px;background:var(--teal);color:var(--white);display:flex;align-items:center;padding:0 110px;justify-content:space-between}
.site-footer ul{list-style:none;display:flex;gap:36px;font-family:"Nunito Sans",sans-serif;font-size:17px}
.site-footer .sub-nav{color:var(--white)}
.copyright{font-size:12px}
.social{display:flex;gap:6px}
.social span{width:24px;height:24px;border:1px solid var(--white);border-radius:50%;display:inline-block}
</style>
</head>
<body>

<header class="section site-header">
  <div class="brand">PetalBooks</div>
  <nav class="main-nav">
    <ul><li>Clients</li><li>Blog</li><li>Contact</li></ul>
    <div class="sub-nav">My Account | Remote Support</div>
  </nav>
</header>

<section class="section hero" role="img" aria-label="Video poster: bookkeeper working at a computer with a spreadsheet">
  <svg class="play" viewBox="0 0 76 76" aria-hidden="true"><circle cx="38" cy="38" r="35" fill="none" stroke="#fff" stroke-width="3"/><path d="M31 24 L54 38 L31 52 Z" fill="#fff"/></svg>
</section>

<section class="section why">
  <h2 class="section-title">Why PetalBooks</h2>
  <p>Well why not? You chose a path of a sole proprietor and self-employment to make money, not waste it spending time sifting through receipts, processing invoices to pay your vendors, and preparing statements for your tax preparer.</p>
  <p>Your time can be better spent growing your business, not bookkeeping for your business. Although we can't proudly call ourselves designers, we've been in the floral industry for many years - washing buckets, cutting boxes, stocking shelves, delivering flowers, not to mention the sleepless holidays. Bookkeeping for a family flower shop started as a hobby, but transformed into an obsession. We understand the hard work and dedication that it takes to operate a successful flower shop and the profitability metrics every shop should strive to meet. Let us manage the stress of bookkeeping so you can focus on customer satisfaction and business growth!</p>
  <div class="btn-row"><a class="btn btn-orange">Get Your Quote</a><a class="btn btn-teal">Sign-up</a></div>
</section>

<section class="section how">
  <h2 class="section-title">Here's how it works</h2>
  <div class="video" role="img" aria-label="Explainer video poster: calculator and paperwork on a desk">
    <svg class="play" viewBox="0 0 76 76" aria-hidden="true"><circle cx="38" cy="38" r="35" fill="none" stroke="#fff" stroke-width="3"/><path d="M31 24 L54 38 L31 52 Z" fill="#fff"/></svg>
  </div>
  <p>We tried hard to make this really simple!<br>After joining our team, we'll send you a scanner and set it up for you. You simply scan your receipts, bills &amp; invoices to us, and we'll send your financial statements at the intervals you need them. Although we won't be printing and sending your bill payments, we'll send them to our payment processor where you'll log in and approve each bill - keeping you in full control of your bank account. Any opportunity we see to save you money, we'll reach out and let you know.<br>It really is that simple!</p>
  <div class="btn-row"><a class="btn btn-orange">Get Your Quote</a><a class="btn btn-teal">Sign-up</a></div>
</section>

<section class="section services">
  <h2 class="section-title">What we do</h2>
  <div class="service-grid">
    <div class="service"><div class="service-icon" role="img" aria-label="Bookkeeping icon: ledger book"></div><h4>Bookkeeping</h4><p>If you send us a receipt, it'll be attached to its respective ledger transaction. Audit proofing your books is our goal.</p></div>
    <div class="service"><div class="service-icon" role="img" aria-label="Payroll icon: money bag"></div><h4>Payroll</h4><p>Payments &amp; payroll taxes guaranteed error free. If there's ever an issue, we will represent you before the tax office.</p></div>
    <div class="service"><div class="service-icon" role="img" aria-label="Sales tax icon: percentage dial"></div><h4>Sales Tax</h4><p>We'll update tax rates when they change. Sales tax deposits and tax filings guaranteed to be sent penalty free.</p></div>
    <div class="service"><div class="service-icon" role="img" aria-label="Financial statements icon: charts on a screen"></div><h4>Financial Statements</h4><p>Financial statements tell a story, let us help you make it a good one. With our metrics, you'll know where you can save money.</p></div>
    <div class="service"><div class="service-icon" role="img" aria-label="Accounts payable icon: briefcase"></div><h4>Accounts Payable</h4><p>Send us your bills and invoices, we'll account for them and let you know when they are ready for your approval. You keep control of your bank account.</p></div>
    <div class="service"><div class="service-icon" role="img" aria-label="Reconciliations icon: devices"></div><h4>Reconciliations</h4><p>We'll update tax rates when they change. Sales tax deposits and tax filings guaranteed to be sent penalty free.</p></div>
  </div>
  <a class="btn-outline">More Services</a>
</section>

<section class="section outsourced">
  <h2>Outsourced bookkeeping? Whoa!</h2>
  <p>Yeah, thanks to the cloud - it's a thing!<br>In-house bookkeeping can become expensive - and although that bookkeeper sitting in your office doesn't seem to bother too much, there are costs associated with that space, equipment and software they are using. Think of the things you can do with that space, perhaps there is a need to expand your work space, or it's a perfect location for a new floral designer that can generate income, not an expense! Let's not even talk about employing a full-time bookkeeper!</p>
  <p>According to the Bureau of Labor Statistics, the median annual wage for a bookkeeper was $38,390 in May 2016. Unless your shop's annual revenue is well above $2 million dollars, employing a full-time bookkeeper is not cost effective. This doesn't even factor any other associated costs related to industry specific training.</p>
  <p>An outsourced bookkeeper can work in their own space and use their own equipment, thus saving you time and money (isn't this the goal?)</p>
</section>

<section class="section cost">
  <div class="cost-text">
    <h2>So, what does it cost you say?!</h2>
    <p>Slow down! We'll get there. First let's talk about what you get and how start with PetalBooks. We want you to rest assured that our costs to you will remain fixed for the term of our agreement and for only the services you need. That's right, no surprise fees or added billable hours. You pay for only the services you need.</p>
    <p class="lead">Once you become our client, you'll get a:</p>
    <ol>
      <li>DeskScan 500 Scanner</li>
      <li>Accounting Software Subscription</li>
      <li>Payroll Subscription</li>
      <li>Accounts Payable Subscription</li>
    </ol>
  </div>
  <div class="cost-photo" role="img" aria-label="Photo of a business professional working at a laptop"></div>
</section>

<section class="section pricing">
  <h2 class="section-title">Pricing Table</h2>
  <div class="price-grid">
    <div class="plan basic"><h3>BASIC PLAN</h3><ul><li>Monthly bank reconciliation</li><li>Receipt scanning included</li><li>Sales tax return filing</li><li>Quarterly financial review</li><li>Email support weekdays</li></ul><div class="price">$35.99</div><a class="btn btn-orange">BUY NOW</a></div>
    <div class="plan advanced"><h3>ADVANCED PLAN</h3><ul><li>Monthly bank reconciliation</li><li>Receipt scanning included</li><li>Sales tax return filing</li><li>Quarterly financial review</li><li>Email support weekdays</li></ul><div class="price">$65.99</div><a class="btn btn-green">BUY NOW</a></div>
    <div class="plan business"><h3>BUSINESS PLAN</h3><ul><li>Monthly bank reconciliation</li><li>Receipt scanning included</li><li>Sales tax return filing</li><li>Quarterly financial review</li><li>Email support weekdays</li></ul><div class="price">$95.99</div><a class="btn btn-teal">BUY NOW</a></div>
  </div>
</section>

<section class="section contact">
  <h2>Still not convinced?</h2>
  <div class="contact-form">
    <div class="fields">
      <div class="field">Shop Name</div>
      <div class="field">Website Address</div>
      <div class="field">Your Name</div>
      <div class="field">Telephone Number</div>
      <div class="field">E-mail</div>
    </div>
    <div class="dropzone">Drag and drop your statement here</div>
  </div>
  <a class="submit">SUBMIT</a>
</section>

<section class="section partners">
  <span class="partner"><i></i>LedgerLeaf</span>
  <span class="partner">PayTrail</span>
  <span class="partner">DocNest</span>
  <span class="partner">ShiftMate</span>
</section>

<section class="section blogs">
  <h2 class="section-title">Our Blogs</h2>
  <div class="blog-grid">
    <article class="post"><div class="post-img" role="img" aria-label="Blog photo: workspace with laptop"><div class="post-date">02<small>MAR</small></div></div><div class="post-body"><h4>Your Blog Title here</h4><p>Short notes on keeping a flower shop's books tidy through the busy holiday season and beyond.</p><a>READ MORE</a></div></article>
    <article class="post"><div class="post-img" role="img" aria-label="Blog photo: person writing at a desk"><div class="post-date">04<small>MAR</small></div></div><div class="post-body"><h4>Your Blog Title here</h4><p>Short notes on keeping a flower shop's books tidy through the busy holiday season and beyond.</p><a>READ MORE</a></div></article>
    <article class="post"><div class="post-img" role="img" aria-label="Blog photo: notebook and coffee"><div class="post-date">07<small>MAR</small></div></div><div class="post-body"><h4>Your Blog Title here</h4><p>Short notes on keeping a flower shop's books tidy through the busy holiday season and beyond.</p><a>READ MORE</a></div></article>
  </div>
</section>

<footer class="section site-footer">
  <div><ul><li>Clients</li><li>Blog</li><li>Contact</li></ul><div class="sub-nav">My Account | Remote Support</div></div>
  <div class="copyright">© 2017 Company Name. All rights reserved</div>
  <div class="social"><span></span><span></span><span></span><span></span></div>
</footer>

</body>
</html>
```